Blue Heron Journeys

We are a predominantly online travel agency with high-end (first/business class) clients. I'm looking to either have our existing logo revamped or a new logo created with business card layout. I prefer to work with existing logo if possible so it remains familiar with existing clientele. I have uploaded a yellow business card layout showing icons on one side of the card. I would like to keep my existing colours, not yellow. could the company name/tag line go over the icons?
Industry/Entity Type
Business
Contact Information for Business Card
Lucinda Fairley
Director
(I.A.T.A. 07715463)
(Corvano Pty. Ltd) ABN 61 574 203 918
512/18 Kendrick Lane
Wattle Reach | NSW 2577 | Australia
www.blueheronjourneys.com.au
m: + 61 (0) 417 588 130
t: + 61 (0) 2 9416 2058
e: lucinda@blueheronjourneys.com.au

```html
<!DOCTYPE html>
<html lang="en">
<head>
<meta charset="utf-8">
<title>Blue Heron Journeys – Business Card Concept 1.01</title>
<link href="https://fonts.googleapis.com/css2?family=Open+Sans:wght@700&family=Raleway:wght@400;500;600;700&display=swap" rel="stylesheet">
<style>
  :root {
    --page: #ffffff;
    --ink: #111111;
    --panel: #404040;
    --panel-edge: #2e2e2e;
    --card: #ffffff;
    --icon-disc: #8c8c8c;
    --brand: #5a5a5a;
    --text: #1e1e1e;
    --on-dark: #ffffff;
  }
  * { margin: 0; padding: 0; box-sizing: border-box; }
  html, body { width: 846px; height: 1200px; overflow: hidden; background: var(--page); }
  .sheet { position: relative; width: 846px; height: 1200px; }

  .concept-title {
    position: absolute; top: 30px; left: 0; width: 100%;
    text-align: center;
    font: 700 58px/1 "Open Sans", sans-serif;
    color: var(--ink);
    letter-spacing: 1px;
  }

  .card {
    position: absolute;
    width: 624px; height: 404px;
    background: var(--card);
    border: 1.5px solid var(--ink);
    box-shadow: 0 6px 8px rgba(0,0,0,0.35);
    overflow: hidden;
  }
  .card-front { left: 126px; top: 138px; }
  .card-back  { left: 118px; top: 597px; }
  .card svg.backdrop { position: absolute; inset: 0; }

  .brand-name {
    position: absolute;
    font-family: "Raleway", sans-serif;
    font-weight: 600;
    color: var(--brand);
    white-space: nowrap;
  }
  .card-front .brand-name { left: 38px; top: 68px; font-size: 18px; }
  .card-back .brand-name {
    left: 378px; top: 215px; font-size: 30px;
    transform: translate(-50%, -50%);
  }

  .holder {
    position: absolute; left: 354px; top: 50px;
    color: var(--on-dark);
    font-family: "Raleway", sans-serif;
  }
  .holder-name { font-weight: 700; font-size: 35px; line-height: 1; }
  .holder-role { font-weight: 500; font-size: 19px; letter-spacing: 3.4px; margin-top: 4px; padding-left: 3px; }

  .contact-list { list-style: none; position: absolute; left: 28px; top: 0; }
  .contact-item {
    position: absolute; left: 0;
    display: flex; align-items: center;
    font: 500 17px/1.25 "Raleway", sans-serif;
    color: var(--text);
    white-space: nowrap;
  }
  .contact-item svg { width: 38px; height: 38px; flex: none; margin-right: 14px; }
  .contact-item.address { top: 143px; }
  .contact-item.email   { top: 199px; }
  .contact-item.phone   { top: 255px; }
  .contact-item.web     { top: 311px; }
  .contact-item.phone span, .contact-item.web span { padding-left: 2px; }
</style>
</head>
<body>
<main class="sheet">
  <h1 class="concept-title">CONCEPT 1.01</h1>

  <section class="card card-front" aria-label="Card front">
    <svg class="backdrop" width="624" height="404" viewBox="0 0 624 404">
      <polygon points="272,0 624,0 624,404 395,404" fill="var(--panel)"/>
    </svg>

    <div class="brand-name">Blue Heron Journeys</div>

    <div class="holder">
      <div class="holder-name">Your Name</div>
      <div class="holder-role">Your Position</div>
    </div>

    <ul class="contact-list">
      <li class="contact-item address">
        <svg viewBox="0 0 38 38" aria-hidden="true">
          <circle cx="19" cy="19" r="19" fill="var(--icon-disc)"/>
          <path d="M19 8c-4.4 0-7.5 3.3-7.5 7.4 0 5.3 7.5 14.2 7.5 14.2s7.5-8.9 7.5-14.2C26.5 11.3 23.4 8 19 8z" fill="#fff"/>
          <circle cx="19" cy="15.5" r="2.8" fill="var(--icon-disc)"/>
        </svg>
        <span>Your Address<br>Street Location,City</span>
      </li>
      <li class="contact-item email">
        <svg viewBox="0 0 38 38" aria-hidden="true">
          <circle cx="19" cy="19" r="19" fill="var(--icon-disc)"/>
          <rect x="9.5" y="12" width="19" height="14" fill="none" stroke="#fff" stroke-width="2"/>
          <path d="M9.5 12l9.5 8 9.5-8M9.5 26l7-6.5M28.5 26l-7-6.5" fill="none" stroke="#fff" stroke-width="1.8"/>
        </svg>
        <span>YourName@Mailbox.com</span>
      </li>
      <li class="contact-item phone">
        <svg viewBox="0 0 38 38" aria-hidden="true">
          <circle cx="19" cy="19" r="19" fill="var(--icon-disc)"/>
          <path d="M13.5 9.5l3.2 4.6-2.1 2.4c1.3 3 3.6 5.3 6.7 6.8l2.3-2.1 4.7 3.1-1.6 3.7c-.4.8-1.3 1.2-2.2 1-7-1.8-12.2-7-14-14-.2-.9.2-1.8 1-2.2z" fill="#fff"/>
        </svg>
        <span>000 111 222 333</span>
      </li>
      <li class="contact-item web">
        <svg viewBox="0 0 38 38" aria-hidden="true">
          <circle cx="19" cy="19" r="19" fill="var(--icon-disc)"/>
          <g fill="none" stroke="#fff" stroke-width="1.8">
            <circle cx="19" cy="19" r="9.5"/>
            <ellipse cx="19" cy="19" rx="4.2" ry="9.5"/>
            <path d="M9.5 19h19M11 14h16M11 24h16"/>
          </g>
        </svg>
        <span>www.YourCompany.com</span>
      </li>
    </ul>
  </section>

  <section class="card card-back" aria-label="Card back">
    <svg class="backdrop" width="624" height="404" viewBox="0 0 624 404">
      <rect width="624" height="404" fill="var(--panel)"/>
      <path d="M186 0 Q40 202 186 404 L624 404 L624 0 Z" fill="var(--panel-edge)"/>
      <path d="M194 0 Q50 202 194 404 L624 404 L624 0 Z" fill="var(--card)"/>
    </svg>
    <div class="brand-name">Blue Heron Journeys</div>
  </section>
</main>
</body>
</html>
```